Flat bootstrap design for existing site

I'm looking for a modern flat design based around an existing logo. This has to be a custom design (no external templates), and implemented into a bootstrap framework.

The logo is attached as 2 versions - choose whichever you want, that flows better with whatever design you choose.

Added screenshots of the existing site (currently using the default bootstrap layouts). Please make your designs around those pages in the screenshots (i.e. the homepage only has the postal code input and the header). The active page has 3 screenshots, because I wanted to illustrate the other states that would be visible (in the table rows).

This is a moving/junk removal website, just for some context.

Here's some example websites (flat designs) that I like, just to give you an idea of what I'm after.

https://www.plimvora.com/
https://dacklow.com/
https://trevanu.com/
https://quobrintal.com/en/

Coding

Coded - Design and coding required

Number of Pages Required

5+ page

Colors

Designer to choose colors to be used in the design.

Requirements
Must have
• It must be a modern/simple flat design, that is built around the existing logo (attached).
• It has to be implemented using bootstrap.

```html
<!DOCTYPE html>
<html lang="en">
<head>
<meta charset="utf-8">
<title>Haulvex – Book Junk Removal</title>
<link href="https://fonts.googleapis.com/css2?family=Open+Sans:wght@400;500;600;700&display=swap" rel="stylesheet">
<style>
  :root {
    --accent: #4bc8f5;
    --primary: #2669a3;
    --page-bg: #f8f8f8;
    --surface: #ffffff;
    --line: #e3e3e3;
    --field-line: #d8d8d8;
    --text: #333333;
    --muted: #666666;
  }
  * { box-sizing: border-box; margin: 0; padding: 0; }
  html, body {
    width: 1200px; height: 902px; overflow: hidden;
    font-family: "Open Sans", sans-serif;
    background: var(--page-bg); color: var(--text);
  }
  .page { position: relative; width: 1200px; height: 902px; }

  .site-header {
    position: absolute; top: 0; left: 0; width: 1200px; height: 88px;
    background: var(--surface);
    border-top: 3px solid var(--accent);
    border-bottom: 1px solid var(--line);
  }
  .brand {
    position: absolute; left: 131px; top: 0; height: 85px;
    display: flex; align-items: center; gap: 8px;
    font-weight: 700; font-size: 30px; letter-spacing: 1px;
    color: var(--accent); text-decoration: none;
  }
  .brand-dot { width: 14px; height: 14px; border-radius: 50%; background: var(--accent); }

  .main-nav { position: absolute; top: 0; left: 0; height: 85px; width: 1200px; }
  .main-nav a {
    position: absolute; top: 0; height: 85px;
    display: flex; align-items: center; justify-content: center;
    font-size: 13px; font-weight: 400; color: var(--muted);
    text-decoration: none; text-transform: uppercase; white-space: nowrap;
  }
  .nav-book { left: 560px; width: 80px; }
  .nav-how { left: 677px; width: 120px; }
  .nav-driver { left: 825px; width: 173px; background: var(--accent); color: var(--surface) !important; }
  .nav-signin { left: 1006px; width: 80px; }

  .booking-card {
    position: absolute; left: 132px; top: 121px; width: 936px; height: 211px;
    background: var(--surface); border: 1px solid var(--line);
    text-align: center;
  }
  .booking-title {
    margin-top: 44px; font-size: 34px; font-weight: 500;
    letter-spacing: -0.2px; color: var(--text); white-space: nowrap;
  }
  .booking-form {
    position: absolute; left: 205px; top: 113px;
    display: flex; gap: 4px;
  }
  .postal-input {
    width: 429px; height: 39px; border: 1px solid var(--field-line); border-radius: 2px;
    padding: 0 11px; font-family: inherit; font-size: 12px; color: var(--muted);
    background: var(--surface);
  }
  .postal-input::placeholder { color: #777; }
  .book-button {
    width: 91px; height: 38px; margin-top: 1px; border: 0; border-radius: 2px;
    background: var(--primary); color: var(--surface);
    font-family: inherit; font-weight: 600; font-size: 14px;
  }

  .site-footer {
    position: absolute; left: 0; top: 845px; width: 1200px; height: 57px;
    background: var(--surface); border-top: 1px solid var(--line);
    display: flex; align-items: center; justify-content: center;
    font-size: 11.5px; color: var(--muted);
  }
</style>
</head>
<body>
<div class="page">
  <header class="site-header">
    <a class="brand" href="#"><span class="brand-dot"></span>HAULVEX</a>
    <nav class="main-nav">
      <a class="nav-book" href="#">Book</a>
      <a class="nav-how" href="#">How it works</a>
      <a class="nav-driver" href="#">Become a driver</a>
      <a class="nav-signin" href="#">Sign in</a>
    </nav>
  </header>

  <main class="booking-card">
    <h1 class="booking-title">Need Junk Removed? Book Now.</h1>
    <form class="booking-form">
      <input class="postal-input" type="text" placeholder="Postel Code">
      <button class="book-button" type="button">BOOK</button>
    </form>
  </main>

  <footer class="site-footer">Copyrights © Haulvex . 2017 | All rights reserved.</footer>
</div>
</body>
</html>
```